Business Card Design Project

Business Card
We are rebranding with a new logo
Industry/Entity Type
Business
Contact Information for Business Card
Dennis Morvale +61 487215963 dennis@quorv.com.au P.O. Box 872 Fernlow QLD 4309
Requirements
Must have
- Logo

```html
<!DOCTYPE html>
<html lang="en">
<head>
<meta charset="utf-8">
<title>Quorv International – Business Card</title>
<link href="https://fonts.googleapis.com/css2?family=Roboto:wght@400;500&family=Roboto+Condensed:wght@700&display=swap" rel="stylesheet">
<style>
  :root {
    --page-bg: #d9d9d9;
    --card-bg: #f4f4f4;
    --brand-blue: #1a8fc9;
    --rule-grey: #555a5e;
    --text-grey: #5a5d60;
    --icon-blue: #1a8fc9;
  }
  html, body {
    margin: 0;
    padding: 0;
    width: 1200px;
    height: 960px;
    overflow: hidden;
    background: var(--page-bg);
  }
  .card {
    position: absolute;
    left: 314px;
    top: 294px;
    width: 600px;
    height: 343px;
    border-radius: 18px;
    background: var(--card-bg);
    font-family: "Roboto", Arial, sans-serif;
    color: var(--text-grey);
  }
  .brand {
    position: absolute;
    left: 34px;
    top: 120px;
    display: flex;
    align-items: center;
    gap: 10px;
  }
  .brand-dot {
    width: 18px;
    height: 18px;
    border-radius: 50%;
    background: var(--brand-blue);
  }
  .brand-name {
    font-family: "Roboto", Arial, sans-serif;
    font-weight: 500;
    font-size: 26px;
    letter-spacing: 1px;
    color: var(--brand-blue);
  }
  .holder-name {
    position: absolute;
    right: 35px;
    top: 163px;
    margin: 0;
    font-family: "Roboto Condensed", "Arial Narrow", sans-serif;
    font-weight: 700;
    font-size: 20px;
    color: var(--brand-blue);
    text-transform: uppercase;
  }
  .divider {
    position: absolute;
    left: 35px;
    right: 35px;
    top: 195px;
    height: 3px;
    background: var(--rule-grey);
  }
  .address {
    position: absolute;
    left: 34px;
    top: 214px;
    margin: 0;
    font-size: 14px;
    line-height: 19px;
    font-style: normal;
  }
  .contacts {
    position: absolute;
    left: 34px;
    top: 258px;
    margin: 0;
    padding: 0;
    list-style: none;
    font-size: 14px;
    line-height: 19px;
  }
  .contacts li {
    display: flex;
    align-items: center;
    gap: 8px;
  }
  .contacts svg {
    width: 13px;
    height: 13px;
    fill: var(--icon-blue);
  }
</style>
</head>
<body>
  <div class="card">
    <div class="brand">
      <span class="brand-dot"></span>
      <span class="brand-name">Quorv International</span>
    </div>

    <h1 class="holder-name">Dennis Morvale</h1>
    <div class="divider"></div>

    <address class="address">P.O. Box 872<br>Fernlow QLD 4309</address>

    <ul class="contacts">
      <li>
        <svg viewBox="0 0 24 24" aria-hidden="true"><path d="M6.6 10.8a15.1 15.1 0 0 0 6.6 6.6l2.2-2.2a1 1 0 0 1 1-.25 11.4 11.4 0 0 0 3.6.57 1 1 0 0 1 1 1V20a1 1 0 0 1-1 1A17 17 0 0 1 3 4a1 1 0 0 1 1-1h3.5a1 1 0 0 1 1 1c0 1.25.2 2.45.57 3.6a1 1 0 0 1-.25 1z"/></svg>
        <span>+61 487215963</span>
      </li>
      <li>
        <svg viewBox="0 0 24 24" aria-hidden="true"><path d="M2 5h20v14H2z M3.5 6.5 12 13l8.5-6.5" fill="none" stroke="var(--icon-blue)" stroke-width="0"/><path d="M2 5h20v2l-10 7L2 7z"/><path d="M2 9l10 7 10-7v10H2z"/></svg>
        <span>dennis@quorv.com.au</span>
      </li>
      <li>
        <svg viewBox="0 0 24 24" aria-hidden="true"><circle cx="12" cy="12" r="10"/><path d="M7 8c2 0 3 1 3 3s2 2 2 4-1 3-1 4M14 4c0 2 1 3 3 3s2 2 3 3" fill="none" stroke="#f4f4f4" stroke-width="1.6"/></svg>
        <span>www.quorv.com.au</span>
      </li>
    </ul>
  </div>
</body>
</html>
```